Northfield Builders Guild Business card

We are looking for a new business card design with photo included.
Our business is a nonprofit construction contractor membership organization. We offer business education, assist with business setup and licensing, provide safety training, and provide a member directory.
URL: www.builderslinkguild.org
Color code:
CMYK: 0 cyan, 42 magenta, 100 yellow, 0 black for Print.
Hexidecimal: #FF9900
RGB: R 255; G 153; B 0

```html
<!DOCTYPE html>
<html lang="en">
<head>
<meta charset="utf-8">
<title>Northfield Builders Guild – Business Card</title>
<link href="https://fonts.googleapis.com/css2?family=Montserrat:wght@400;500;800&display=swap" rel="stylesheet">
<style>
  :root{
    --orange:#F7941F;
    --charcoal:#383638;
    --white:#ffffff;
    --rule:#8d8b8d;
    --backdrop:#e3e3e3;
  }
  *{margin:0;padding:0;box-sizing:border-box}
  html,body{width:1200px;height:1200px;overflow:hidden}
  body{background:var(--backdrop);font-family:'Montserrat',sans-serif;position:relative}
  .card{position:absolute;left:200px;width:800px;height:457px;border-radius:26px;overflow:hidden}
  .card-front{top:120px;background:var(--charcoal)}
  .card-back{top:630px;background:var(--orange)}

  .front-top{position:absolute;left:0;top:0;width:100%;height:220px;background:var(--white);border-bottom:5px solid var(--orange)}
  .brand-name{position:absolute;right:72px;top:58px;text-align:right;font-weight:800;color:var(--charcoal);font-size:38px;line-height:42px;letter-spacing:-0.5px;text-transform:uppercase}

  .person{position:absolute;left:52px;top:258px}
  .person-name{color:var(--orange);font-weight:500;font-size:27px;line-height:30px;letter-spacing:0.3px;text-transform:uppercase}
  .person-title{color:var(--white);font-size:18px;line-height:22px;font-weight:500}
  .divider{position:absolute;left:52px;top:316px;width:695px;height:2px;background:var(--rule)}

  .contacts{position:absolute;left:52px;top:329px;list-style:none}
  .contacts li{display:flex;align-items:center;height:22.7px;color:var(--white);font-size:18.5px;font-weight:500}
  .contacts svg{width:16px;height:16px;margin-right:11px;fill:var(--orange);flex:none}

  .address{position:absolute;right:54px;top:327px;text-align:right;color:var(--white);font-size:18.5px;line-height:22.5px;font-weight:500;font-style:normal}

  .back-brand{position:absolute;left:0;width:100%;top:155px;text-align:center;font-weight:800;color:var(--charcoal);font-size:54px;line-height:58px;letter-spacing:-1px;text-transform:uppercase}
  .back-url{position:absolute;left:0;width:100%;top:377px;text-align:center;color:var(--white);font-size:18px;letter-spacing:3.6px}
</style>
</head>
<body>
  <section class="card card-front" aria-label="Business card front">
    <div class="front-top">
      <div class="brand-name">Northfield<br>Builders Guild</div>
    </div>
    <div class="person">
      <div class="person-name">Daniel Reyes</div>
      <div class="person-title">President</div>
    </div>
    <div class="divider"></div>
    <ul class="contacts">
      <li><svg viewBox="0 0 16 16" aria-hidden="true"><path d="M3.2 1.5l2.4 2.6-1.3 1.8c.9 2 2.6 3.7 4.6 4.6l1.8-1.3 2.6 2.4-1.6 2.4C6.6 13.6 2.4 9.4 1.2 3.1z"/></svg>(555) 214-7730</li>
      <li><svg viewBox="0 0 16 16" aria-hidden="true"><path d="M4 1h8v14H4zM5.5 2.5v9.5h5V2.5z"/></svg>555.380.1942</li>
      <li><svg viewBox="0 0 16 16" aria-hidden="true"><path d="M1 4h14v9H1zM2.5 5.2v.6L8 9.3l5.5-3.5v-.6z"/></svg>support@nbguild.org</li>
      <li><svg viewBox="0 0 16 16" aria-hidden="true"><circle cx="8" cy="8" r="7"/></svg>builderslinkguild.org</li>
    </ul>
    <address class="address">2400 Meridian Ave<br>Suite #210<br>Fairhaven, OR 97000</address>
  </section>

  <section class="card card-back" aria-label="Business card back">
    <div class="back-brand">Northfield<br>Builders Guild</div>
    <div class="back-url">www.builderslinkguild.org</div>
  </section>
</body>
</html>
```